Meadowrun Acres Website Design

We have been redeveloping our website already and are quite happy with the content, but the design needs to be better:
https://tilvexa-hub.examplehost.net/

Pages, content, concept etc. Can all be taken from the redeveloped website.
The farmer can register and edit/view their profile, subscribe and these pages need to be designed better as well as contact, about, pricing, tos, privacy and a page with example portlets.

We need a website to appeal to farmers, investors and retiring farmers.

The design should be clean and a little country.

We don't want any repeat designs that some may submit to every project and has no respect for the project brief, so please don't submit them.

Target Market(s)

farmers, investors, retirees

Industry/Entity Type

Farming

Number of Pages Required

5+ page

Colors

Designer to choose colors to be used in the design.

Requirements
Must have
• Nice, clean modern design that is appealing
• Profile page laid out nicely

```html
<!DOCTYPE html>
<html lang="en">
<head>
<meta charset="utf-8">
<title>Pricing | Meadowrun Acres</title>
<link rel="stylesheet" href="https://fonts.googleapis.com/css2?family=Questrial&family=Roboto:wght@400;500;700&display=swap">
<style>
:root{
  --green:#3aaa35;
  --green-dark:#2f9a2b;
  --orange:#f7860b;
  --ink:#2b2b2b;
  --text:#555;
  --muted:#777;
  --rule:#e6e6e6;
  --panel-dark:#3b3b3b;
  --footer:#3a3a3a;
  --footer-text:#bdbdbd;
  --crumb:#f2f2f2;
  --white:#fff;
}
*{box-sizing:border-box;margin:0;padding:0}
html,body{width:1200px;height:2426px;overflow:hidden}
body{position:relative;background:var(--white);font-family:"Roboto",Arial,sans-serif;color:var(--text)}

/* Header */
.site-header{position:absolute;top:0;left:0;width:1200px;height:94px;background:var(--white);z-index:3}
.brand-badge{position:absolute;left:81px;top:16px;width:105px;height:105px;border-radius:50%;background:var(--white);display:flex;align-items:center;justify-content:center;text-align:center;z-index:4}
.brand-badge span{font-family:"Roboto",sans-serif;font-weight:700;font-size:14px;line-height:1.2;color:var(--green)}
.main-nav{position:absolute;left:225px;top:38px;display:flex;gap:20px}
.main-nav a{font-weight:500;font-size:14.5px;color:#333;text-decoration:none;letter-spacing:.2px;padding-bottom:4px}
.main-nav a.active{color:var(--green);border-bottom:2px solid var(--green)}
.account-link{position:absolute;left:946px;top:38px;font-weight:500;font-size:14.5px;color:var(--orange);display:flex;align-items:center;gap:8px}

/* Hero */
.hero{position:absolute;top:94px;left:0;width:1200px;height:254px;background:linear-gradient(100deg,#4c5a3a 0%,#6f7f4d 25%,#8c9c6a 45%,#4f6a55 65%,#6b8fa8 85%,#3f5a44 100%)}
.hero h1{position:absolute;top:100px;width:100%;text-align:center;font-family:"Questrial",sans-serif;font-weight:400;font-size:44px;color:var(--white)}
.breadcrumb{position:absolute;top:348px;left:0;width:1200px;height:40px;background:var(--crumb);padding-left:73px;font-size:15px;line-height:40px;color:#444}
.breadcrumb a{color:var(--green);text-decoration:none}

.section-title{position:absolute;left:0;width:1200px;text-align:center;font-family:"Questrial",sans-serif;font-size:26px;color:var(--ink)}

/* Plan cards */
.plan{position:absolute;top:509px;width:332px;height:764px;background:var(--green);border-radius:4px;padding:0 12px 12px}
.plan-name{height:65px;line-height:65px;padding-left:6px;font-family:"Roboto",sans-serif;font-weight:500;font-size:20px;color:var(--white)}
.plan-body{position:relative;height:687px;background:var(--white);border-radius:8px;padding:56px 8px 0}
.plan-price{position:absolute;top:-25px;right:13px;width:134px;height:134px;border-radius:50%;background:var(--orange);color:var(--white);text-align:center;padding-top:27px;z-index:2}
.plan-price .amount{font-size:40px;font-weight:700;line-height:1}
.plan-price .amount sup{font-size:22px;vertical-align:top;position:relative;top:2px}
.plan-price .per{font-size:24px;line-height:1.1}
.plan-intro{font-size:14px;color:#444;padding:0 6px 4px}
.feature-list{list-style:none}
.feature-list li{display:flex;gap:10px;align-items:flex-start;padding:10px 6px;border-bottom:1px solid var(--rule);font-size:14px;line-height:1.55;color:#555}
.feature-list li:last-child{border-bottom:0}
.feature-list svg{flex:0 0 19px;margin-top:2px}
.btn{display:block;background:var(--orange);color:var(--white);text-align:center;font-weight:500;font-size:14px;text-transform:uppercase;letter-spacing:.3px;border-radius:2px;text-decoration:none}
.plan .btn{position:absolute;left:7px;right:7px;bottom:18px;height:41px;line-height:41px}

/* Dark boxes */
.box{position:absolute;top:1329px;height:312px;border:2px solid var(--panel-dark);border-radius:4px;background:var(--panel-dark);padding:0 8px 8px}
.box-title{height:50px;line-height:50px;padding-left:8px;font-weight:500;font-size:20px;color:var(--white)}
.box-body{position:relative;height:252px;background:var(--white);border-radius:8px;padding:12px 10px 0}
.box .btn{position:absolute;left:2px;right:2px;bottom:6px;height:40px;line-height:40px}
.free{font-family:"Roboto",sans-serif;font-weight:500;font-size:26px;color:var(--ink)}
.box .plan-intro{padding:2px 8px 2px;font-size:14px}
.box .feature-list li{padding:9px 8px}
.donate-text{text-align:center;font-size:18px;line-height:30px;color:#444;padding:30px 36px 0}

/* Match fees */
.subtitle{position:absolute;top:1739px;width:1200px;text-align:center;font-size:14px;color:#555}
.fee{position:absolute;top:1800px;width:340px}
.fee-icon{position:absolute;left:0;top:4px;width:64px;height:64px;border-radius:6px;background:#3a3a3a}
.fee h3{position:absolute;left:108px;top:0;font-family:"Roboto",sans-serif;font-weight:500;font-size:20px;color:var(--ink)}
.fee p{position:absolute;left:108px;top:36px;width:230px;font-size:14.5px;line-height:22.5px;color:#666}

/* Footer */
.site-footer{position:absolute;top:2086px;left:0;width:1200px;height:340px;background:linear-gradient(180deg,#3d3d3d,#333)}
.footer-heading{position:absolute;top:34px;font-weight:500;font-size:16px;color:var(--white)}
.post{position:absolute;left:73px;width:340px;height:64px}
.post-date{position:absolute;left:0;top:0;width:61px;height:64px;background:var(--green);border:2px solid #fff;color:var(--white);text-align:center}
.post-date .day{display:block;font-weight:700;font-size:28px;line-height:34px;margin-top:4px}
.post-date .mon{display:block;font-size:11px;line-height:14px}
.post-title{position:absolute;left:81px;top:0;width:260px;font-weight:500;font-size:16px;line-height:22px;color:var(--white)}
.post-by{position:absolute;left:81px;top:46px;font-size:13px;color:var(--footer-text)}
.news-text{position:absolute;left:496px;top:72px;width:330px;font-size:14.5px;line-height:22px;color:var(--footer-text)}
.news-input{position:absolute;left:496px;top:130px;width:332px;height:36px;border-radius:18px;background:var(--white);padding-left:16px;font-size:14px;line-height:36px;color:#999}
.news-btn{position:absolute;left:496px;top:178px;width:129px;height:36px;border-radius:18px;background:var(--orange);color:var(--white);text-align:center;font-weight:500;font-size:16px;line-height:36px}
.col-rule{position:absolute;top:30px;width:1px;height:220px;background:#4a4a4a}
.footer-brand{position:absolute;left:868px;top:160px;width:270px;text-align:center;font-family:"Roboto",sans-serif;font-weight:500;font-size:24px;color:#cfcfcf}
.footer-bar{position:absolute;left:73px;top:272px;width:1052px;height:1px;background:#4a4a4a}
.legal{position:absolute;left:73px;top:302px;font-size:13px;color:var(--footer-text)}
.social{position:absolute;top:290px;width:30px;height:30px;border-radius:50%;background:#8a8a8a}
</style>
</head>
<body>
<svg width="0" height="0" style="position:absolute" aria-hidden="true">
  <symbol id="tick-grey" viewBox="0 0 20 20"><circle cx="10" cy="10" r="8.5" fill="none" stroke="#777" stroke-width="1.6"/><path d="M6 10.2l3 3 6-7" fill="none" stroke="#777" stroke-width="1.8" stroke-linecap="round" stroke-linejoin="round"/></symbol>
  <symbol id="tick-green" viewBox="0 0 20 20"><circle cx="10" cy="10" r="8.5" fill="none" stroke="#3aaa35" stroke-width="1.6"/><path d="M6 10.2l3 3 6-7" fill="none" stroke="#3aaa35" stroke-width="1.8" stroke-linecap="round" stroke-linejoin="round"/></symbol>
</svg>

<header class="site-header">
  <nav class="main-nav">
    <a href="#">HOME</a><a href="#">ASPIRING FARMERS</a><a href="#">INVESTORS</a><a href="#">RETIRING FARMER</a><a href="#">BLOG</a><a href="#" class="active">PRICING</a><a href="#">CONTACT</a>
  </nav>
  <div class="account-link">
    <svg width="16" height="16" viewBox="0 0 16 16"><path d="M9 2h5v12H9M2 8h8M7 5l3 3-3 3" fill="none" stroke="#f7860b" stroke-width="1.6" stroke-linecap="round" stroke-linejoin="round"/></svg>
    SIGN IN OR SIGN UP
  </div>
</header>
<div class="brand-badge"><span>Meadowrun<br>Acres</span></div>

<section class="hero" role="img" aria-label="Photo of a farming family with young children outdoors among trees">
  <h1>Pricing</h1>
</section>
<div class="breadcrumb"><a href="#">Home</a> / Pricing</div>

<h2 class="section-title" style="top:420px">Aspiring Farmers</h2>

<article class="plan" style="left:73px">
  <div class="plan-price"><div class="amount"><sup>$</sup>50</div><div class="per">/year</div></div>
  <div class="plan-name">Starter</div>
  <div class="plan-body">
    <ul class="feature-list">
      <li><svg width="19" height="19"><use href="#tick-grey"/></svg>Public profile</li>
      <li><svg width="19" height="19"><use href="#tick-grey"/></svg>Stories of success</li>
      <li><svg width="19" height="19"><use href="#tick-grey"/></svg>Tips on how to get farm ready</li>
      <li><svg width="19" height="19"><use href="#tick-grey"/></svg>Part of a movement of new farmers across Australia</li>
      <li><svg width="19" height="19"><use href="#tick-grey"/></svg>Updates on farm opportunities</li>
    </ul>
    <a class="btn" href="#">Register</a>
  </div>
</article>

<article class="plan" style="left:433px">
  <div class="plan-price"><div class="amount"><sup>$</sup>150</div><div class="per">/year</div></div>
  <div class="plan-name">Aspiring Farmer</div>
  <div class="plan-body">
    <p class="plan-intro">All of free membership as well as:</p>
    <ul class="feature-list">
      <li><svg width="19" height="19"><use href="#tick-green"/></svg>Eligible for farm opportunities</li>
      <li><svg width="19" height="19"><use href="#tick-green"/></svg>We help find you great education, training and job opportunities (at discounted rates)</li>
      <li><svg width="19" height="19"><use href="#tick-green"/></svg>Support in finding your own dream farm through a retiring farmer you know</li>
      <li><svg width="19" height="19"><use href="#tick-green"/></svg>Free Vendora market analysis membership (valued at $300 pa)</li>
      <li><svg width="19" height="19"><use href="#tick-green"/></svg>Farm business webinars (valued at $200)</li>
      <li><svg width="19" height="19"><use href="#tick-green"/></svg>Corporate Partner Opportunities</li>
      <li><svg width="19" height="19"><use href="#tick-green"/></svg>Public or Private profile (as required)</li>
      <li><svg width="19" height="19"><use href="#tick-green"/></svg>Eligible to enter competitions and win prizes</li>
    </ul>
    <a class="btn" href="#">Register</a>
  </div>
</article>

<article class="plan" style="left:794px">
  <div class="plan-price"><div class="amount"><sup>$</sup>400</div><div class="per">/year</div></div>
  <div class="plan-name">Farm Ready</div>
  <div class="plan-body">
    <ul class="feature-list">
      <li><svg width="19" height="19"><use href="#tick-grey"/></svg>All of Aspiring Farmer as well as</li>
      <li><svg width="19" height="19"><use href="#tick-grey"/></svg>We promote your profile on our blog and social media</li>
      <li><svg width="19" height="19"><use href="#tick-grey"/></svg>4 half hour phone sessions with the Meadowrun Acres team to help you get farm-ready</li>
      <li><svg width="19" height="19"><use href="#tick-grey"/></svg>We review your profile and offer tips for improvement</li>
      <li><svg width="19" height="19"><use href="#tick-grey"/></svg>We review your education requirements and find you the best next opportunities</li>
      <li><svg width="19" height="19"><use href="#tick-grey"/></svg>You will be selected for any publicity opportunities that arise</li>
      <li><svg width="19" height="19"><use href="#tick-grey"/></svg>Profile promotion on home page for 3 months of the year</li>
      <li><svg width="19" height="19"><use href="#tick-green"/></svg>Meadowrun Acres team on tap for advice</li>
      <li><svg width="19" height="19"><use href="#tick-green"/></svg>We will find you a farm mentor</li>
    </ul>
    <a class="btn" href="#">Register</a>
  </div>
</article>

<article class="box" style="left:73px;width:513px">
  <div class="box-title">Investor &amp; Retiree</div>
  <div class="box-body">
    <div class="free">Free</div>
    <p class="plan-intro">All of free membership as well as:</p>
    <ul class="feature-list">
      <li><svg width="19" height="19"><use href="#tick-green"/></svg>Support in negotiating farm opporunities</li>
      <li><svg width="19" height="19"><use href="#tick-green"/></svg>Corporate partner opportunities</li>
      <li><svg width="19" height="19"><use href="#tick-green"/></svg>Any other great deals we can find</li>
    </ul>
    <a class="btn" href="#">Register</a>
  </div>
</article>

<article class="box" style="left:614px;width:511px">
  <div class="box-title">Donate</div>
  <div class="box-body">
    <p class="donate-text">If you want to rejuvenate regional Australia then consider donating to us. We will love you forever and any donation over $50 we will get an aspiring farmer to write you a personalised message</p>
    <a class="btn" href="#">Donate now and help us make this a reality.</a>
  </div>
</article>

<h2 class="section-title" style="top:1689px">Match Making Fees</h2>
<p class="subtitle">We will charge a success fee for when you are matched on your farm:</p>

<div class="fee" style="left:73px">
  <div class="fee-icon" role="img" aria-label="Icon of a group of people"></div>
  <h3>Aspiring Farmer</h3>
  <p>You will be charged a match-making fee upon the successful placement onto your farm. Depending on the arrangement, this will be a maximum of $2,000.</p>
</div>
<div class="fee" style="left:433px">
  <div class="fee-icon" role="img" aria-label="Icon of hands holding money"></div>
  <h3>Investor</h3>
  <p>If you need farmers, we charge a fee to find the farmer you need. This can be as involved or hands off as you require. Our only requirement is that we will be ensuring that the new farmer is able to meet their dreams of farm ownership and management and we will support them through this.</p>
</div>
<div class="fee" style="left:794px">
  <div class="fee-icon" role="img" aria-label="Icon of a farmer with a pitchfork"></div>
  <h3>Retiring Farmer</h3>
  <p>You will be charged a match-making fee upon the successful placement of a new farmer and investors into your farm. Depending on the arrangement, this will be a maximum of $5,000</p>
</div>

<footer class="site-footer">
  <div class="footer-heading" style="left:73px">From The Blog</div>
  <div class="post" style="top:81px">
    <div class="post-date"><span class="day">24</span><span class="mon">APR 17</span></div>
    <div class="post-title">Out of the Griddle House into the fire of soil health | Tom Ashby</div>
    <div class="post-by">Posted by Tom Ashby</div>
  </div>
  <div class="post" style="top:178px">
    <div class="post-date"><span class="day">21</span><span class="mon">APR 17</span></div>
    <div class="post-title">Wesley is a cool name, so is Maren, but their passion for farming</div>
    <div class="post-by">Posted by Wesley and Maren</div>
  </div>
  <div class="col-rule" style="left:462px"></div>
  <div class="footer-heading" style="left:496px">Subscribe To Our Newsletter</div>
  <p class="news-text">Want to be the first to know about our amazing discount offer?</p>
  <div class="news-input">Email Address</div>
  <div class="news-btn">Subscribe</div>
  <div class="col-rule" style="left:868px"></div>
  <div class="footer-brand">Meadowrun Acres</div>
  <div class="footer-bar"></div>
  <p class="legal">©2017 Meadowrun Acres. Terms of Use | Privay | Sitemap | Donate</p>
  <span class="social" style="left:1020px"></span>
  <span class="social" style="left:1057px"></span>
  <span class="social" style="left:1094px"></span>
</footer>
</body>
</html>
```